Business card for builder specialising in renovations.

Need a card for our building business. Business name is under Martin Powles.
Have licence number on card ( 527691K)
Contact number (0400 382 415)
Want to work on logo for some business cards and shirts - something with MP or MPB or open to ideas??
No animations, No hammers. Something sharp and eye catching.
Highlight that we are a renovation specialist. Simple on front with extra details on back with some lines to jot down things.

Target Market(s)

Renovators

Industry/Entity Type

Building

Contact Information for Business Card

2 sided with room on back to jot things down.
Extra details on back so front can be simple ..like, renovations, bathrooms, decks, extensions, new builds,

Logo Text

MP

Font styles to use
Serif

Requirements
Must have
• Eye catching design .
• Name : Martin powles
• Licence number
• Contact number - 0400382415
Nice to have
• Some logo design that we can carry through to other forms of advertising
• Local builder
• Quality work
Should not have
• No animations

```html
<!DOCTYPE html>
<html lang="en">
<head>
<meta charset="utf-8">
<title>Martin Powles – Business Card</title>
<link rel="stylesheet" href="https://fonts.googleapis.com/css2?family=Tinos:wght@400;700&display=swap">
<style>
  :root {
    --bg: #2b2b2d;
    --card-dark: #050505;
    --card-light: #ffffff;
    --brand-blue: #29a8e0;
    --ink: #111111;
    --paper-white: #ffffff;
  }
  * { box-sizing: border-box; margin: 0; padding: 0; }
  html, body {
    width: 1200px; height: 900px; overflow: hidden;
    background: var(--bg);
    font-family: "Tinos", "Times New Roman", serif;
  }
  .canvas { position: relative; width: 1200px; height: 900px; }

  .card {
    position: absolute;
    width: 640px; height: 366px;
    box-shadow: 0 14px 30px rgba(0,0,0,.45);
    overflow: hidden;
  }

  /* Front */
  .card--front { left: 80px; top: 60px; background: var(--card-dark); }
  .front-brand {
    position: absolute; left: 70px; top: 120px;
    display: flex; flex-direction: column; gap: 12px;
  }
  .brand-lockup { display: flex; align-items: center; gap: 14px; }
  .brand-square {
    width: 46px; height: 46px; background: var(--brand-blue); flex: none;
  }
  .brand-name {
    font-size: 30px; font-weight: 400; letter-spacing: .5px;
    color: var(--brand-blue); text-transform: uppercase; line-height: 1;
  }
  .front-web { font-size: 17px; color: var(--paper-white); padding-left: 60px; }
  .front-web .accent { color: var(--brand-blue); }

  .service-list {
    position: absolute; left: 420px; top: 112px;
    list-style: none; display: flex; flex-direction: column; gap: 8px;
  }
  .service-list li {
    display: flex; align-items: center; gap: 12px;
    font-size: 15px; color: var(--brand-blue);
    text-transform: uppercase; letter-spacing: .3px;
  }
  .service-list li::before {
    content: ""; width: 11px; height: 11px; background: var(--paper-white); flex: none;
  }

  /* Back */
  .card--back { left: 480px; top: 470px; background: var(--card-light); }
  .back-brand {
    position: absolute; right: 48px; top: 36px;
    display: flex; align-items: center; gap: 12px;
  }
  .back-brand .brand-square { width: 40px; height: 40px; }
  .back-brand .brand-name { font-size: 22px; color: var(--ink); }
  .rule {
    position: absolute; left: 205px; right: 40px; top: 130px;
    height: 1px; background: var(--brand-blue);
  }
  .edge-tab {
    position: absolute; left: 0; top: 208px;
    width: 34px; height: 30px; background: var(--ink);
  }
  .contact { position: absolute; left: 52px; top: 186px; color: var(--ink); }
  .contact-name {
    font-size: 28px; color: var(--brand-blue);
    text-transform: uppercase; line-height: 1;
  }
  .contact-role { font-size: 15px; margin-top: 6px; }
  .contact-licence { font-size: 16px; margin-top: 3px; }
  .contact-licence .label { color: var(--brand-blue); }
  .contact-lines { list-style: none; margin-top: 4px; }
  .contact-lines li {
    display: flex; align-items: center; gap: 10px;
    font-size: 16px; line-height: 22px;
  }
  .contact-lines svg { width: 12px; height: 12px; flex: none; }
  .contact-lines .accent { color: var(--brand-blue); }
</style>
</head>
<body>
<main class="canvas">

  <section class="card card--front" aria-label="Card front">
    <div class="front-brand">
      <div class="brand-lockup">
        <span class="brand-square"></span>
        <span class="brand-name">Martin Powles</span>
      </div>
      <div class="front-web">www.<span class="accent">mpbuilds</span>.com</div>
    </div>
    <ul class="service-list">
      <li>Renovations</li>
      <li>Bathrooms Decks</li>
      <li>Extensions</li>
      <li>New Builds</li>
    </ul>
  </section>

  <section class="card card--back" aria-label="Card back">
    <div class="back-brand">
      <span class="brand-square"></span>
      <span class="brand-name">Martin Powles</span>
    </div>
    <div class="rule"></div>
    <div class="edge-tab"></div>
    <div class="contact">
      <div class="contact-name">Martin Powles</div>
      <div class="contact-role">Director</div>
      <div class="contact-licence"><span class="label">Licence:</span> (527691K)</div>
      <ul class="contact-lines">
        <li>
          <svg viewBox="0 0 12 12" aria-hidden="true"><path d="M3 1 L5 3.5 L4 5 Q5 7 7 8 L8.5 7 L11 9 L9.5 11 Q5 11 2.5 7.5 Q1 5 1.5 2.5 Z" fill="#29a8e0"/></svg>
          0400382415
        </li>
        <li>
          <svg viewBox="0 0 12 12" aria-hidden="true"><rect x="1" y="2.5" width="10" height="7" fill="none" stroke="#29a8e0" stroke-width="1.2"/><path d="M1 2.5 L6 6.5 L11 2.5" fill="none" stroke="#29a8e0" stroke-width="1.2"/></svg>
          info@mpbuilds.com
        </li>
        <li>
          <svg viewBox="0 0 12 12" aria-hidden="true"><circle cx="6" cy="6" r="5" fill="none" stroke="#29a8e0" stroke-width="1.1"/><ellipse cx="6" cy="6" rx="2.2" ry="5" fill="none" stroke="#29a8e0" stroke-width="1"/><path d="M1 6 H11" stroke="#29a8e0" stroke-width="1"/></svg>
          www.<span class="accent">mpbuilds</span>.com
        </li>
      </ul>
    </div>
  </section>

</main>
</body>
</html>
```